Kinesiology undergraduate program needs an infographic

We would like an infographic to creatively and succinctly inform students, faculty, staff, and others about our undergraduate values and competencies (perhaps also integrating our mission and vision). We would like to see a design that incorporates the definition of Kinesiology (the study of human movement) and the colors of our Westbrook State University at Harlan.

```html
<!DOCTYPE html>
<html lang="en">
<head>
<meta charset="utf-8">
<title>Westbrook State University at Harlan – Kinesiology Undergraduate Program</title>
<link rel="stylesheet" href="https://fonts.googleapis.com/css2?family=Bebas+Neue&family=Roboto:wght@400;700;900&display=swap">
<style>
  :root {
    --red: #e0202a;
    --navy: #1f2350;
    --ink: #2e2e33;
    --cyan: #1aa6c8;
    --rule: #b9b9bd;
    --margin: #e5737a;
    --paper: #ffffff;
  }
  * { box-sizing: border-box; margin: 0; padding: 0; }
  html, body { width: 1200px; height: 848px; overflow: hidden; background: var(--paper); }
  .sheet {
    position: relative; width: 1200px; height: 848px; overflow: hidden;
    font-family: "Roboto", Arial, sans-serif; color: var(--ink);
    background:
      linear-gradient(90deg, transparent 143px, var(--margin) 143px, var(--margin) 145px, transparent 145px,
        transparent 152px, var(--margin) 152px, var(--margin) 154px, transparent 154px),
      repeating-linear-gradient(180deg, transparent 0 18px, var(--rule) 18px 20px, transparent 20px 33.5px);
  }
  .runner-figure {
    position: absolute; left: 345px; top: 232px; width: 490px; height: 616px;
    background: radial-gradient(ellipse at 62% 45%, #b5443a 0%, #cf8a78 30%, rgba(214,214,218,.85) 58%, rgba(255,255,255,0) 78%);
    border-radius: 40% 40% 10% 10%;
  }
  .headline {
    position: absolute; font-family: "Bebas Neue", Impact, sans-serif; color: var(--red);
    font-size: 50px; line-height: 1; letter-spacing: 1px; text-align: center;
  }
  .statement { position: absolute; text-align: center; font-size: 15.5px; line-height: 20px; color: var(--ink); }
  .mission-title { left: 0; width: 1200px; top: 54px; }
  .mission-text { left: 400px; width: 400px; top: 104px; }
  .values-title { left: 130px; width: 205px; top: 194px; }
  .values-text { left: 100px; width: 265px; top: 242px; }
  .vision-title { left: 872px; width: 210px; top: 194px; }
  .vision-text { left: 845px; width: 265px; top: 242px; }
  .competency { position: absolute; font-size: 15.5px; line-height: 20.6px; }
  .competency h3 { font-weight: 900; font-size: 15.5px; color: var(--navy); text-transform: uppercase; line-height: 19px; }
  .competency ul { list-style: none; }
  .intrapersonal { left: 124px; top: 493px; }
  .science { left: 124px; top: 653px; }
  .thinking { left: 861px; top: 493px; }
  .relationships { left: 861px; top: 653px; }
  .graphics { position: absolute; left: 0; top: 0; }
</style>
</head>
<body>
<main class="sheet">
  <div class="runner-figure" role="img" aria-label="Illustration of a sprinting athlete shown half as a pale body form and half as an anatomical muscle figure, with motion blur"></div>

  <h1 class="headline mission-title">Our Mission</h1>
  <p class="statement mission-text">To empower undergraduate students to pursue excellence through scientific discovery, clinical practice, and health promotion</p>

  <h2 class="headline values-title">Our Values</h2>
  <p class="statement values-text">Student Success, Science, and Service<br>Our Graduates Will Be Competent In…</p>

  <h2 class="headline vision-title">Our Vision</h2>
  <p class="statement vision-text">WSUH Kinesiology graduates are leaders who excel in careers that enhance the quality of life of individuals and communities</p>

  <svg class="graphics" width="1200" height="848" viewBox="0 0 1200 848" aria-hidden="true">
    <g fill="none" stroke="var(--navy)" stroke-width="2">
      <!-- connectors -->
      <polyline points="356,399 97,399 97,496"/>
      <polyline points="313,663 392,663 392,613 413,613"/>
      <polyline points="781,382 805,382 805,496 855,496"/>
      <polyline points="748,570 801,570 801,663 855,663"/>
    </g>
    <g fill="var(--navy)">
      <circle cx="356" cy="399" r="5"/><circle cx="97" cy="496" r="5"/>
      <circle cx="313" cy="663" r="5"/><circle cx="413" cy="613" r="5"/>
      <circle cx="781" cy="382" r="5"/><circle cx="855" cy="496" r="5"/>
      <circle cx="748" cy="570" r="5"/><circle cx="855" cy="663" r="5"/>
      <polygon points="217,341 233,341 225,353"/>
    </g>

    <!-- pencil icon -->
    <g transform="translate(110,420) rotate(45 28 28)" fill="none" stroke="var(--navy)" stroke-width="3">
      <rect x="20" y="-6" width="16" height="52"/>
      <polygon points="20,46 36,46 28,62" fill="var(--navy)"/>
      <line x1="20" y1="4" x2="36" y2="4"/>
    </g>
    <!-- heartbeat -->
    <polyline fill="none" stroke="var(--navy)" stroke-width="2"
      points="180,450 215,450 222,440 228,462 236,420 244,474 250,450 290,450 297,440 303,462 311,420 319,474 325,450 365,450 372,440 378,462 386,420 394,474 400,450 428,450"/>

    <!-- atom icon -->
    <g transform="translate(75,659)" fill="none" stroke="var(--navy)" stroke-width="3">
      <ellipse rx="30" ry="11"/>
      <ellipse rx="30" ry="11" transform="rotate(60)"/>
      <ellipse rx="30" ry="11" transform="rotate(-60)"/>
      <circle r="5" fill="var(--navy)"/>
    </g>

    <!-- pie icons -->
    <g>
      <circle cx="427" cy="655" r="21" fill="var(--navy)"/>
      <path d="M427 655 L427 634 A21 21 0 0 1 446 664 Z" fill="#fff"/>
      <path d="M427 655 L446 664 A21 21 0 0 1 410 667 Z" fill="var(--red)"/>
      <circle cx="427" cy="655" r="8" fill="var(--cyan)"/>
      <circle cx="427" cy="718" r="21" fill="var(--red)"/>
      <path d="M427 718 L427 697 A21 21 0 0 1 448 718 Z" fill="var(--navy)"/>
      <circle cx="427" cy="718" r="8" fill="var(--cyan)"/>
      <circle cx="427" cy="777" r="21" fill="var(--navy)"/>
      <path d="M427 777 L448 777 A21 21 0 0 1 410 789 Z" fill="var(--red)"/>
      <path d="M427 777 L410 789 A21 21 0 0 1 406 777 Z" fill="#fff"/>
      <circle cx="427" cy="777" r="8" fill="var(--cyan)"/>
    </g>

    <!-- weekly line chart -->
    <g font-family="Roboto, Arial, sans-serif" font-size="8" fill="var(--ink)">
      <text x="812" y="407">20:00</text><text x="812" y="422">16:00</text>
      <text x="812" y="437">12:00</text><text x="812" y="452">8:00</text>
      <g stroke="#d6d6d6" stroke-width="1">
        <line x1="838" y1="404" x2="1112" y2="404"/><line x1="838" y1="419" x2="1112" y2="419"/>
        <line x1="838" y1="434" x2="1112" y2="434"/><line x1="838" y1="449" x2="1112" y2="449"/>
      </g>
      <text x="857" y="466">Mon</text><text x="894" y="466">Tue</text><text x="928" y="466">Wed</text>
      <text x="965" y="466">Thu</text><text x="1001" y="466">Fri</text><text x="1033" y="466">Sat</text><text x="1070" y="466">Sun</text>
    </g>
    <path fill="none" stroke="var(--red)" stroke-width="2"
      d="M840 434 C852 420 866 418 876 428 S892 440 902 426 S918 432 928 424 S948 400 960 402 S976 410 986 414 S1004 432 1014 420 S1030 396 1044 404 S1060 432 1072 430 S1100 436 1112 438"/>

    <!-- lightbulb icon -->
    <g transform="translate(1125,474)" fill="none" stroke="var(--navy)" stroke-width="3">
      <path d="M-11 14 C-11 4 -19 -1 -19 -12 A19 19 0 0 1 19 -12 C19 -1 11 4 11 14 Z"/>
      <line x1="-9" y1="21" x2="9" y2="21"/><line x1="-7" y1="28" x2="7" y2="28"/>
      <path d="M-5 14 L-5 0 L5 0 L5 14" stroke-width="2"/>
      <line x1="-36" y1="-12" x2="-27" y2="-12"/><line x1="27" y1="-12" x2="36" y2="-12"/>
      <line x1="-28" y1="-35" x2="-21" y2="-28"/><line x1="28" y1="-35" x2="21" y2="-28"/>
      <line x1="0" y1="-44" x2="0" y2="-36"/>
    </g>

    <!-- radiating circle icon -->
    <g transform="translate(1098,666)" fill="none" stroke="var(--navy)" stroke-width="3">
      <circle r="38"/>
      <circle r="27" stroke-width="2"/>
      <circle r="11"/>
      <g stroke-width="2">
        <line x1="0" y1="-14" x2="0" y2="-22"/><line x1="0" y1="14" x2="0" y2="22"/>
        <line x1="-14" y1="0" x2="-22" y2="0"/><line x1="14" y1="0" x2="22" y2="0"/>
        <line x1="10" y1="10" x2="16" y2="16"/><line x1="-10" y1="-10" x2="-16" y2="-16"/>
        <line x1="10" y1="-10" x2="16" y2="-16"/><line x1="-10" y1="10" x2="-16" y2="16"/>
      </g>
    </g>

    <!-- progress bar -->
    <line x1="829" y1="819" x2="1200" y2="819" stroke="var(--red)" stroke-width="4"/>
    <line x1="829" y1="819" x2="952" y2="819" stroke="var(--cyan)" stroke-width="4"/>
    <line x1="952" y1="819" x2="1076" y2="819" stroke="var(--cyan)" stroke-width="4"/>
    <line x1="952" y1="819" x2="1000" y2="819" stroke="var(--red)" stroke-width="4"/>
    <circle cx="829" cy="819" r="7" fill="var(--cyan)"/>
    <circle cx="952" cy="819" r="7" fill="var(--cyan)" stroke="#fff" stroke-width="2"/>
    <circle cx="1076" cy="819" r="8" fill="var(--navy)" stroke="var(--cyan)" stroke-width="3"/>
  </svg>

  <section class="competency intrapersonal">
    <h3>Intrapersonal Growth</h3>
    <ul><li>Cultural Humility/Sensitivity</li><li>Integrity</li><li>Self-Directed</li><li>Dependability</li><li>Mission Oriented</li></ul>
  </section>
  <section class="competency science">
    <h3>The Science of<br>Kinesiology</h3>
    <ul><li>Foundational Concepts of</li><li>Kinesiology</li><li>Clinical Application</li><li>Scientific Communication</li></ul>
  </section>
  <section class="competency thinking">
    <h3>Thinking and Reasoning</h3>
    <ul><li>Critical Thinking</li><li>Quantitative Reasoning</li><li>Scientific Inquiry</li><li>Concept Integration</li></ul>
  </section>
  <section class="competency relationships">
    <h3>Relationships and<br>Communication</h3>
    <ul><li>Cultural Competence</li><li>Professionalism</li><li>Leadership and Teamwork</li><li>Service</li><li>Orientation/Citizenship</li></ul>
  </section>
</main>
</body>
</html>
```